Electrician Letterhead Design MVR

We need some letterhead for our bills and other papers.
Customer address is on the right side (Swiss format)
A4 format

Design should also be applicable on Cards

Target Market(s)

Private Customers, Small Business

Industry/Entity Type

Electrician

Other font styles liked:
• incised 901

Colors
00AB8E
00BBA5
67D7C9
C6EFE9
E9F9F6

```html
<!DOCTYPE html>
<html lang="en">
<head>
<meta charset="utf-8">
<title>MVR Letterhead</title>
<link href="https://fonts.googleapis.com/css2?family=Lato:wght@400;700;900&family=Great+Vibes&display=swap" rel="stylesheet">
<style>
  :root {
    --teal: #00a08c;
    --teal-light: #7ccdc2;
    --ink: #2b2b2b;
    --paper: #ffffff;
    --backdrop: #e6e9ec;
  }
  * { margin: 0; padding: 0; box-sizing: border-box; }
  html, body { width: 1200px; height: 725px; overflow: hidden; background: var(--backdrop); }
  body { font-family: 'Lato', sans-serif; color: var(--ink); }

  .letterhead {
    position: absolute; left: 350px; top: 22px;
    width: 500px; height: 680px;
    background: var(--paper);
    box-shadow: 0 2px 10px rgba(0,0,0,.18);
    overflow: hidden;
  }
  .brand { position: absolute; left: 38px; top: 30px; }
  .brand-row { display: flex; align-items: center; gap: 6px; }
  .brand-name { font-size: 44px; font-weight: 900; color: var(--teal); line-height: 1; letter-spacing: 1px; }
  .brand-mark { width: 12px; height: 12px; background: var(--teal); }
  .brand-tagline { font-size: 7.4px; font-weight: 700; margin-top: 4px; letter-spacing: .2px; }

  .contact { position: absolute; left: 347px; top: 30px; font-size: 8px; line-height: 10.6px; }
  .contact .address { margin-bottom: 4px; }
  .contact-line { display: flex; align-items: center; gap: 4px; line-height: 11.5px; }
  .contact-line svg { width: 7px; height: 7px; fill: var(--teal); flex: none; }

  .header-rule { position: absolute; left: 37px; top: 103px; width: 424px; height: 1.5px; background: var(--teal); }

  .letter { position: absolute; left: 38px; top: 149px; width: 423px; font-size: 9px; line-height: 10.5px; }
  .letter .date { margin-bottom: 12px; }
  .letter .block { margin-bottom: 11px; }
  .letter .salutation { font-size: 11.5px; font-weight: 700; margin: 2px 0 10px; }
  .letter p.body { text-align: justify; margin-bottom: 10.5px; }
  .letter .closing { margin-top: 22px; }
  .signature { font-family: 'Great Vibes', cursive; font-size: 24px; margin-top: 10px; line-height: 1; }

  .footer-wave { position: absolute; left: 0; bottom: 0; width: 500px; height: 74px; }
</style>
</head>
<body>
  <main class="letterhead">
    <div class="brand">
      <div class="brand-row">
        <span class="brand-name">MVR</span>
        <span class="brand-mark"></span>
      </div>
      <div class="brand-tagline">Elektrotechnik Marder GmbH</div>
    </div>

    <div class="contact">
      <div class="address">42-07 Linden Row 14,<br>Fairhaven, NY 11402</div>
      <div class="contact-line">
        <svg viewBox="0 0 10 10"><path d="M2 1h2l1 2.5-1.2 1a5 5 0 0 0 2.7 2.7l1-1.2L10 7v2c0 .6-.4 1-1 1A9 9 0 0 1 0 2c0-.6.4-1 1-1z"/></svg>
        <span>555-210-4378</span>
      </div>
      <div class="contact-line">
        <svg viewBox="0 0 10 10"><path d="M0 2h10v6H0z M0 2l5 3.5L10 2" stroke="#fff" stroke-width=".8"/></svg>
        <span>info@examplemail.com</span>
      </div>
      <div class="contact-line">
        <svg viewBox="0 0 10 10"><circle cx="5" cy="5" r="5"/><path d="M0 5h10M5 0c-2.5 3-2.5 7 0 10M5 0c2.5 3 2.5 7 0 10" stroke="#fff" stroke-width=".7" fill="none"/></svg>
        <span>www.examplewebsite.com</span>
      </div>
    </div>

    <div class="header-rule"></div>

    <section class="letter">
      <div class="date">Feb-03-2022</div>
      <div class="block">Mr, John Doe<br>President</div>
      <div class="block">Harbor Works Inc.<br>123 Street Name, Suite# 10<br>City, State, 120023</div>
      <div class="salutation">Dear Mr, John</div>
      <p class="body">Lorem ipsum dolor sit amet, consectetur adipisicing elit, sed do eiusmod tempor incididunt ut labore et dolore magna aliqua. Ut enim ad minim veniam, quis nostrud exercitation ullamco laboris nisi ut aliquip ex ea commodo consequat. Duis aute irure dolor in reprehenderit in voluptate velit esse cillum dolore eu fugiat nulla pariatur.</p>
      <p class="body">Lorem ipsum dolor sit amet, consectetur adipisicing elit, sed do eiusmod tempor incididunt ut labore et dolore magna aliqua. Ut enim ad minim veniam, quis nostrud exercitation ullamco laboris nisi ut aliquip ex ea commodo consequat. Duis aute irure dolor in reprehenderit in voluptate velit esse cillum dolore eu fugiat nulla pariatur.</p>
      <p class="body">Lorem ipsum dolor sit amet, consectetur adipisicing elit, sed do eiusmod tempor incididunt ut labore et dolore magna aliqua. Ut enim ad minim veniam, quis nostrud exercitation ullamco laboris nisi ut aliquip ex ea commodo consequat.</p>
      <p class="body">Excepteur sint occaecat cupidatat non proident, sunt in culpa qui officia deserunt mollit anim id est laborum. re et dolore magnam aliquam quaerat voluptatem.</p>
      <div class="closing">Regards</div>
      <div class="signature">Daniel Reeve</div>
    </section>

    <svg class="footer-wave" viewBox="0 0 500 74" preserveAspectRatio="none" aria-hidden="true">
      <path d="M310 40 C390 42 460 34 500 6 L500 17 C455 38 385 44 310 40 Z" fill="var(--teal-light)"/>
      <path d="M0 36 C80 10 170 8 260 26 C350 44 440 44 500 22 L500 74 L0 74 Z" fill="var(--teal)"/>
    </svg>
  </main>
</body>
</html>
```